UI design for an Zyn(Halvo) photo editing app

This design contest is to design the UI/screenshots of an Zyn(Halvo) app named "Kestrel Pix". Some minor design details are left out at this point as the mockup is still in progress. The icon of this app will be designed separately. The winner of this job will be selected to work on a long term basis as an Dorvo version and several updates will have to be designed as well as the Quillex version. Please take
this as a long term opportunity.
The photo app is called "Kestrel Pix". The design need to dynamic, different that stands out WITH a serious and polished look.
All the mockups and sample screenshots are attached for ease. Please thoroughly review them.
This app has the following screens:
1. Welcome screen(just a simple background will do now as icon will be put later).
2. Main Screen (or LightBox)
The background of this screen can be the same as the background of the welcome screen. It can be a wooden background OR a background of your
choice that fits and blends in the buttons and fonts/colors.
The main screen has this bars/buttons/options that has separate screens:
On top, menu bar:
has these buttons
settings on the left(icon)
in the middle, 3 buttons (please check lightbox mockup and lightbox sample pics)
on the right, share icon(check share screen sample)
Our share options:
"Share" button screenshot:
Our share options:
Save
Email
Copy
Moodlefy
Chatterbay
Zorbly
Quorra
in the middle, just background where the pictures would appear later after importing
or saving
at the bottom bar:
3 buttons:
Camera Roll(on the left)
Camera Button(middle)
Advanced Button(on the right)
2 versions of this screenshot need to be designed.
1. regular version with all the options
2. regular version plus the "steam effect" button showing up on top of the "Advanced" button(mockup with red lines)
3 separate screenshots need to be designed for the options"
settings screenshot(please check sample):
Gift Kestrel Pix to a friend
Rate/review in the Tundle Hub
(space in between...so they are grouped)
Geotagiing(on/off)
Captured photos get location-specific information(these lines in smaller fonts)
Launch in Capture Mode(on/off)
Kestrel Pix is automatically lauched in camera mode
Autosave to Camera Roll(on/off)
Captured photos are directly saved to camera roll
Reset All Tutorials
Tap to reset all the tutorials
In the "Steam Effect" screen, please check the mockup
Top Bar: lightbox button(to go back), heading and Done button
Middle: Steam background(provided)
Bottom bar:
refresh button
droplets(when clicked on/off options show up on top, please check mockup)
finger size(when clicked 3 options show up)
steam density(when clicked 3 options show up)
Please use the buttons for the droplets, finger size and steam density from the steam effects button image provided)
(and also the background of this screenshot(in the middle) would be a steam screen which is provided. Please use the
steam background provided and you need to use the background in the middle, just omit the top and the bottom bar from the image)
Now back to the main(lightbox screen):
When Clicked on the "Camera" in the middle of the bottom bar, the capture mode screen shows up.
Please refer to the mockup first
There you will see the cancel button on the left
camera button in the middle
a small settings button on the right
and a filters button on the right
and the filters bar on the top
ours need to like this
please refer to capture mode sample 1
please refer to capture mode sample 2
please refer to capture mode sample 3
normal
Grid
timer(5/15/30 secs)
Edit Screen(check sample)
Edit options
Adjust:(displayed on a bar)
1. Left
2. Right
3. Horizontal
4. Vertical
5. Straightening
Crop:
None
Original
Golden
Freeform
Square
3:2
4:3
4:6
5:7
8:10
16:9
Filters:(please note that this filter icon and the filter icon in the "capture mode" screenshot need to same)
(the filters are displayed on a bar, please check sample)
There is a sample picture that you need to put in the picture of the filters. It would be same picture in
every filter at this point.
00.None
0.Calibrate
1. aurora
2. drizzle
3. icicle
4. blizzard
5. calm
6. dew
7. knot
8. dry
9. eye
10. flurry
11. fog
12. frost
13. hail
14. haze
15. heat
16. humid
17. overcast
18. polar
19. thermal
20. trace
Editing options on top:(check sample)
Brightness
Contrast
Saturation
Textures:(dispalyed on a bar, check sample)
1.None
2.Bark
3.Grunge1
4.Grunge2
5.grunge3
6.Grunge4
7.Paper
8.Cardboard
9.Wood
10.Bokeh
11.Bricks
12.Metal
13.Asphalt
14.Pavement1
15.Pavement2
16.Paint1
17.Paint2
18.Rust
19.Towel
20.Stone1
21.Stone2
22.Wall
23.Urban1
24.Urban2
25.Urban3
26.Watercolor
Tilt-shift/Vignette:(check sample)
Borders:(check samples, at this point, we are working on them, you just need to make a bar that displays them)
1.None
2.
3.
4.
5.
6.
7.
8.
9.
10.
11.
12.
13.
14.
15.
16.
This is our primary design mockup. Upon selecting the final version, we will be working on some more and minor details(as
we are also working with the coders).
And there is a folder callled "app sample". Please take a look at it and think how our app can be different and stand out.
Thanks and feel free to contact me anytime if you have any questions. Looking forward to hearing from you and building a long term
relationship.
All camera app users who likes to edit their photos with cool tools.
Building

```html
<!DOCTYPE html>
<html lang="en">
<head>
<meta charset="utf-8">
<title>Kestrel Pix – Settings</title>
<link href="https://fonts.googleapis.com/css2?family=Open+Sans:wght@400;600;700;800&display=swap" rel="stylesheet">
<style>
:root{
  --bar-red:#b0121a;
  --bar-red-dark:#6e0208;
  --maroon:#5a0a10;
  --row-bg:#f4f4f4;
  --row-bg-2:#e6e6e6;
  --row-text:#555;
  --dark-row:#505050;
  --dark-row-2:#3e3e3e;
  --white:#fff;
  --check-red:#e0202a;
  --check-off:#b8b8b8;
  --icon:#4a4a4a;
}
*{box-sizing:border-box;margin:0;padding:0}
html,body{width:676px;height:1200px;overflow:hidden}
body{font-family:"Open Sans",Arial,sans-serif;background:#000}
.screen{position:relative;width:676px;height:1200px;overflow:hidden;
  background:radial-gradient(ellipse at 50% 20%,#3c3c3c 0%,#262626 45%,#0c0c0c 100%)}
.top-bar{position:absolute;left:0;top:0;width:676px;height:106px;
  background:linear-gradient(#c0141c,var(--bar-red) 55%,var(--bar-red-dark));
  box-shadow:0 3px 6px rgba(0,0,0,.6)}
.top-bar::after{content:"";position:absolute;left:0;right:0;top:96px;border-top:2px dashed rgba(255,210,210,.55)}
.top-title{position:absolute;left:0;right:0;top:28px;text-align:center;color:var(--white);
  font-size:34px;font-weight:700;text-shadow:0 2px 3px rgba(0,0,0,.6)}
.bar-btn{position:absolute;top:30px;height:49px;border-radius:7px;
  background:linear-gradient(#fafafa,#cfd6de);color:var(--maroon);font-weight:700;font-size:21px;
  display:flex;align-items:center;justify-content:center;box-shadow:0 1px 3px rgba(0,0,0,.5)}
.btn-back{left:34px;width:75px;border-radius:0 7px 7px 0}
.btn-back::before{content:"";position:absolute;left:-12px;top:7px;width:35px;height:35px;transform:rotate(45deg);
  background:linear-gradient(135deg,#fafafa,#cfd6de);border-radius:4px;z-index:-1}
.btn-back span{position:relative;left:-4px}
.btn-save{left:550px;width:89px}
.section-label{position:absolute;left:0;right:0;top:136px;text-align:center;color:var(--white);font-size:22px}
.segmented{position:absolute;left:53px;top:174px;width:545px;height:66px;display:flex;border-radius:5px;overflow:hidden;
  border:2px solid #dfe6ee}
.segmented div{flex:1;display:flex;align-items:center;justify-content:center;color:var(--maroon);font-weight:700;font-size:22px;
  background:linear-gradient(#eef2f6,#a9bccf);border-right:1px solid #8fa3b7}
.segmented div:last-child{border-right:none}
.segmented .active{background:linear-gradient(#fdfdfd,#e8e8e8)}
.row{position:absolute;left:56px;width:537px;display:flex;align-items:center;
  background:linear-gradient(var(--white),var(--row-bg) 60%,var(--row-bg-2));color:var(--row-text)}
.row.dark{background:linear-gradient(#5a5a5a,var(--dark-row) 50%,var(--dark-row-2));color:var(--white);
  border-top:2px solid #8a8a8a}
.row-icon{position:absolute;left:94px;width:38px;height:38px;display:flex;align-items:center;justify-content:center}
.row-label{position:absolute;left:112px;font-weight:700;font-size:18px}
.row-sub{display:block;font-weight:400;font-size:11.5px;margin-top:-2px}
.check{position:absolute;left:470px;width:30px;height:30px;border-radius:4px}
.check.on{background:linear-gradient(#f04048,var(--check-red));border:2px solid #fff;box-shadow:0 0 0 1px #aaa}
.check.off{background:linear-gradient(#d8d8d8,var(--check-off));border:2px solid #eee;box-shadow:0 0 0 1px #999}
.check svg{position:absolute;left:3px;top:3px}
.mark{width:26px;height:26px;border-radius:50%;background:var(--white)}
.row-trail{position:absolute;left:470px;color:#aaa;font-size:30px;font-weight:400}
.reset-btn{position:absolute;left:166px;top:988px;width:317px;height:72px;border-radius:36px;
  background:linear-gradient(#f2f2f2,#bdbdbd);border:3px solid #e5e5e5;box-shadow:0 2px 6px rgba(0,0,0,.7);
  text-align:center;padding-top:13px}
.reset-title{color:var(--white);font-weight:800;font-size:19px;text-shadow:0 1px 2px rgba(0,0,0,.5);line-height:1.05}
.reset-sub{color:var(--check-red);font-size:12px;font-weight:600}
</style>
</head>
<body>
<div class="screen">
  <header class="top-bar">
    <div class="bar-btn btn-back"><span>Back</span></div>
    <div class="top-title">Settings</div>
    <div class="bar-btn btn-save">Save</div>
  </header>

  <div class="section-label">Image Quality</div>
  <div class="segmented"><div>Low</div><div class="active">Medium</div><div>High</div></div>

  <div class="row" style="top:251px;height:67px">
    <div class="row-icon" style="left:38px"><svg width="28" height="28" viewBox="0 0 28 28"><path d="M2 5l7-3 10 3 7-3v21l-7 3-10-3-7 3z" fill="none" stroke="var(--icon)" stroke-width="2.5"/><path d="M9 2v21M19 5v21" stroke="var(--icon)" stroke-width="2"/></svg></div>
    <div class="row-label">GeoTagging<span class="row-sub">Captured photos get location-specific information</span></div>
    <div class="check off"><svg width="20" height="20" viewBox="0 0 20 20"><path d="M4 10l4 4 8-9" fill="none" stroke="#9a9a9a" stroke-width="3"/></svg></div>
  </div>

  <div class="row" style="top:331px;height:66px">
    <div class="row-icon" style="left:38px"><svg width="30" height="28" viewBox="0 0 30 28"><rect x="2" y="2" width="10" height="24" fill="var(--icon)"/><rect x="12" y="7" width="16" height="14" fill="none" stroke="var(--icon)" stroke-width="2.5"/></svg></div>
    <div class="row-label">Camera Roll</div>
    <div class="check on"><svg width="20" height="20" viewBox="0 0 20 20"><path d="M4 10l4 4 8-9" fill="none" stroke="#fff" stroke-width="3"/></svg></div>
  </div>

  <div class="row" style="top:409px;height:66px">
    <div class="row-icon" style="left:38px"><svg width="34" height="28" viewBox="0 0 34 28"><rect x="1" y="6" width="32" height="21" rx="3" fill="var(--icon)"/><rect x="10" y="2" width="14" height="6" rx="2" fill="var(--icon)"/><circle cx="17" cy="16" r="7" fill="#f4f4f4"/><circle cx="17" cy="16" r="4.5" fill="var(--icon)"/></svg></div>
    <div class="row-label">Capture Mode</div>
    <div class="check on"><svg width="20" height="20" viewBox="0 0 20 20"><path d="M4 10l4 4 8-9" fill="none" stroke="#fff" stroke-width="3"/></svg></div>
  </div>

  <div class="row" style="top:488px;height:67px">
    <div class="row-icon" style="left:38px"><svg width="28" height="30" viewBox="0 0 28 30"><path d="M20 6L7 15l13 9" fill="none" stroke="var(--icon)" stroke-width="2.5"/><circle cx="21" cy="5" r="5" fill="var(--icon)"/><circle cx="6" cy="15" r="5" fill="var(--icon)"/><circle cx="21" cy="25" r="5" fill="var(--icon)"/></svg></div>
    <div class="row-label">Share Settings</div>
    <div class="row-trail">+</div>
  </div>

  <div class="row dark" style="top:555px;height:68px">
    <div class="row-icon" style="left:38px"><div class="mark" style="border-radius:5px"></div></div>
    <div class="row-label">Moodlefy</div>
    <div class="check on"><svg width="20" height="20" viewBox="0 0 20 20"><path d="M4 10l4 4 8-9" fill="none" stroke="#fff" stroke-width="3"/></svg></div>
  </div>
  <div class="row dark" style="top:623px;height:68px">
    <div class="row-icon" style="left:38px"><div class="mark"></div></div>
    <div class="row-label">Quorra</div>
    <div class="check off"><svg width="20" height="20" viewBox="0 0 20 20"><path d="M4 10l4 4 8-9" fill="none" stroke="#9a9a9a" stroke-width="3"/></svg></div>
  </div>
  <div class="row dark" style="top:691px;height:68px">
    <div class="row-icon" style="left:38px"><div class="mark"></div></div>
    <div class="row-label">Zorbly</div>
    <div class="check on"><svg width="20" height="20" viewBox="0 0 20 20"><path d="M4 10l4 4 8-9" fill="none" stroke="#fff" stroke-width="3"/></svg></div>
  </div>
  <div class="row dark" style="top:759px;height:69px">
    <div class="row-icon" style="left:38px"><div class="mark" style="border-radius:5px"></div></div>
    <div class="row-label">Chatterbay</div>
    <div class="check off"><svg width="20" height="20" viewBox="0 0 20 20"><path d="M4 10l4 4 8-9" fill="none" stroke="#9a9a9a" stroke-width="3"/></svg></div>
  </div>

  <div class="row" style="top:839px;height:66px">
    <div class="row-icon" style="left:38px"><svg width="34" height="32" viewBox="0 0 34 32"><path d="M17 1l4.8 10.2 11 1.3-8.2 7.6 2.2 11L17 25.6 7.2 31l2.2-11L1.2 12.5l11-1.3z" fill="var(--icon)"/></svg></div>
    <div class="row-label">Rate/Review &nbsp;Kestrel Pix</div>
    <div class="row-trail"><svg width="22" height="24" viewBox="0 0 22 24" style="margin-top:8px"><path d="M3 2l8 0 9 10-9 10-8 0 9-10z" fill="#aaa"/></svg></div>
  </div>

  <div class="reset-btn">
    <div class="reset-title">RESET ALL TUTORIALS</div>
    <div class="reset-sub">Tap to reset all the tutorials</div>
  </div>
</div>
</body>
</html>
```